Web Design Project - Shipping Industry

Goals and Objectives
The objective of the new website is to create a more modern look and feel. The site will also allow for a more effective means of communicating with members while providing the public with information and developments in the local, regional and international shipping industry.
Scope
The website will highlight the history of the organisation inclusive of text and photographs. It will take visitors through the years from beginning to present. Information on the history of the shipping industry will also be included.
It will feature current articles on the organisation, its members and stakeholders in the shipping industry. Member information as well as pertinent details regarding the organisation’s subsidiaries will be documented for the website.
Information as it relates to shipping statistics, case studies, laws and regulations, international treaties and trade documents, shipping terms, careers in shipping, job opportunities, training opportunities, information for shippers including port listing and trade lanes will be main features of the content for the website.
The Association’s community involvement, industry calendar events and related links relevant industry members will also be featured.
Target Market
• The General Public;
• Members of the organization;
• Shipping Industry Stakeholders (local, regional and international);
• Tertiary students conducting research.
• Potential employees
• Potential Business Partners
Best Practice Bench Marketing
The following websites are being looked at:
• Korvel Quayworks - http://www.korvelquayworks.example/ (preferred look)
• Tessaly Maritime Association - http://www.tma-freight.example/ (like image transition on main page)
• Drovna - http://www.drovna.example (professional look)
• PLW - http://www.pelworth.example (preferred color: blue in logo)
• Quillo - http://www.quillo.example/electronics/tv-video-audio/ (preferred look for links page: image + short text below + visit site link)
Expected Result
• 3 - 5 pages which must include: [1] main page [2] standard page [3] links page

```html
<!DOCTYPE html>
<html lang="en">
<head>
<meta charset="utf-8">
<title>Veltrona – Global Shipper</title>
<link rel="stylesheet" href="https://fonts.googleapis.com/css2?family=Arimo:wght@400;700&family=Teko:wght@500;600&display=swap">
<style>
  :root {
    --navy-deep: #0a1a5c;
    --navy: #142a86;
    --blue-page: #3a55c8;
    --white: #ffffff;
    --ink: #3a3a3a;
    --logo-ink: #2a2d6e;
    --accent-orange: #e39a12;
    --heading-blue: #1a3aa8;
    --sub-blue: #1a9ad6;
    --rule: #1d3a6c;
    --panel-grey: #eef0f4;
    --chevron: #c9ccd6;
  }
  * { box-sizing: border-box; margin: 0; padding: 0; }
  html, body { width: 905px; height: 1200px; overflow: hidden; }
  body {
    background: linear-gradient(180deg, var(--navy-deep) 0%, #1e33a0 40%, var(--blue-page) 100%);
    font-family: "Arimo", Arial, sans-serif;
    color: var(--ink);
    position: relative;
  }
  .page { position: absolute; left: 17.5px; top: 0; width: 869px; }

  /* Header */
  .site-header { height: 106px; background: var(--white); position: relative; }
  .brand {
    position: absolute; left: 11px; top: 44px;
    font-size: 29px; letter-spacing: 5px; color: var(--logo-ink);
    font-weight: 400; text-transform: uppercase; line-height: 1;
  }
  .locator-map {
    position: absolute; left: 550px; top: 36px; width: 68px; height: 42px;
    background: radial-gradient(ellipse at center, #3a7de0 0%, #2a5cc8 60%, rgba(42,92,200,0) 72%);
  }
  .locate-link {
    position: absolute; left: 631px; top: 50px;
    font-size: 11.5px; color: var(--accent-orange); text-decoration: none;
  }
  .search-box {
    position: absolute; left: 702px; top: 44px; width: 163px; height: 25px;
    border: 1px solid #c7c9cf; border-radius: 5px;
    background: linear-gradient(180deg, #f1f1f3 0%, #ffffff 45%);
  }
  .search-box svg { position: absolute; right: 8px; top: 6px; }

  /* Navigation */
  .main-nav {
    height: 48px; display: flex;
    background: linear-gradient(180deg, #1f3bb0 0%, #132a8c 55%, #0f2070 100%);
    border-bottom: 2px solid #d7dbe8;
  }
  .main-nav a {
    display: flex; align-items: center; justify-content: center;
    color: var(--white); font-weight: 700; font-size: 11.5px; text-decoration: none;
    border-right: 1px solid #0a1650; height: 100%;
  }
  .main-nav a.current { color: var(--accent-orange); }

  /* Hero */
  .hero { margin-top: 6px; height: 376px; position: relative; background: var(--white); }
  .hero-photo {
    position: absolute; left: 0; top: 0; width: 869px; height: 276px;
    background: linear-gradient(180deg, #c8d3dc 0%, #aebdca 35%, #6f94b4 60%, #2d4a66 100%);
  }
  .hero-caption {
    position: absolute; left: 0; top: 276px; width: 869px; height: 100px;
    background: linear-gradient(180deg, #1c2f78 0%, #17286e 100%);
  }
  .hero-caption h1 {
    position: absolute; left: 26px; top: 14px;
    font-family: "Teko", "Arial Narrow", sans-serif; font-weight: 500;
    font-size: 33px; line-height: 1; color: var(--white); letter-spacing: 0.5px;
  }
  .hero-caption p {
    position: absolute; left: 26px; top: 50px; width: 800px;
    font-size: 11.6px; line-height: 18.5px; color: var(--white);
  }
  .hero-next { position: absolute; left: 808px; top: 19px; }

  /* Content */
  .content { background: var(--white); height: 598px; position: relative; }
  .section-title {
    position: absolute; left: 14.5px; top: 10px; width: 833px; height: 44px;
    background: var(--panel-grey); border-bottom: 2px solid var(--rule);
  }
  .section-title h2 {
    font-family: "Teko", "Arial Narrow", sans-serif; font-weight: 500;
    font-size: 32px; line-height: 1; color: var(--heading-blue);
    position: absolute; left: 11px; top: 11px;
  }
  .article {
    position: absolute; left: 27px; top: 80px; width: 530px;
    font-size: 11.6px; line-height: 16.6px; text-align: justify;
  }
  .article p { margin-bottom: 16.6px; }
  .article h3 {
    font-weight: 400; font-size: 17px; line-height: 20px; color: var(--sub-blue);
    margin: 7px 0 15px;
  }
  .article-photo {
    position: absolute; left: 577.5px; top: 80px; width: 269px; height: 138px;
    background: linear-gradient(180deg, #3a4660 0%, #56606e 45%, #2c55b8 72%, #1b2c50 100%);
  }
  .read-more {
    position: absolute; left: 434.5px; top: 545px; width: 100px; height: 31px;
    display: flex; align-items: center; justify-content: center;
    background: linear-gradient(180deg, #2a3ea8 0%, #0f1f70 100%);
    border-bottom: 2px solid #9aa4c8;
    color: #f1b436; font-size: 12px; text-decoration: none;
  }

  /* Footer */
  .site-footer { height: 64px; position: relative; color: var(--white); }
  .footer-nav { position: absolute; left: 9px; top: 23px; font-size: 11px; }
  .footer-nav a { color: var(--white); text-decoration: none; }
  .footer-nav span { margin: 0 11px; }
  .copyright { position: absolute; left: 493px; top: 24px; font-size: 10.5px; }
  .social { position: absolute; left: 714px; top: 16px; display: flex; gap: 12px; }
  .social span {
    width: 28px; height: 28px; border-radius: 50%;
    background: radial-gradient(circle at 40% 35%, #d8d8dc 0%, #a4a6ae 100%);
    display: block;
  }
</style>
</head>
<body>
<div class="page">
  <header class="site-header">
    <div class="brand">Veltrona</div>
    <div class="locator-map" role="img" aria-label="Small dotted world map icon"></div>
    <a class="locate-link" href="#">Locate Us</a>
    <div class="search-box">
      <svg width="14" height="14" viewBox="0 0 14 14" aria-hidden="true">
        <circle cx="6" cy="6" r="4.5" fill="none" stroke="#b0b3ba" stroke-width="1.6"/>
        <line x1="9.3" y1="9.3" x2="13" y2="13" stroke="#b0b3ba" stroke-width="1.8"/>
      </svg>
    </div>
  </header>

  <nav class="main-nav">
    <a class="current" href="#" style="width:61px">Home</a>
    <a href="#" style="width:80px">About Us</a>
    <a href="#" style="width:103px">Sustainability</a>
    <a href="#" style="width:67px">News</a>
    <a href="#" style="width:78px">Careers</a>
    <a href="#" style="width:66px">Links</a>
    <a href="#" style="width:92px">Contact Us</a>
  </nav>

  <section class="hero">
    <div class="hero-photo" role="img" aria-label="Container ship with light blue hull sailing on open sea under a cloudy sky"></div>
    <div class="hero-caption">
      <h1>GLOBAL SHIPPER</h1>
      <p>Lorem ipsum dolor sit amet, consectetuer adipiscing elit, sed diam nonummy nibh euismod tincidunt ut laoreet dolore magna aliquam erat volutpat.<br>
      Ut wisi enim ad minim veniam, quis nostrud exerci tation ullamcorper suscipit lobortis nisl ut aliquip ex ea commodo consequat.</p>
      <svg class="hero-next" width="40" height="62" viewBox="0 0 40 62" aria-label="Next slide">
        <polygon points="0,0 16,0 40,31 16,62 0,62 24,31" fill="var(--chevron)"/>
      </svg>
    </div>
  </section>

  <main class="content">
    <div class="section-title"><h2>ABOUT US</h2></div>
    <article class="article">
      <p>Lorem Ipsum is simply dummy text of the printing and typesetting industry. Lorem Ipsum has been the industry's standard dummy text ever since the 1500s, when an unknown printer took a galley of type and scrambled it to make a type specimen book. It has survived not only five centuries, but also the leap into electronic typesetting, remaining essentially unchanged. It was popularised in the 1960s with the release of Printrex sheets containing Lorem Ipsum passages, and more recently with desktop publishing software like Pressly Layout including versions of Lorem Ipsum</p>
      <p>Contrary to popular belief, Lorem Ipsum is not simply random text. It has roots in a piece of classical Latin literature from 45 BC, making it over 2000 years old. Harold Brenwick, a Latin professor at Ashcombe College in Virginia, looked up one of the more obscure Latin words, consectetur, from a Lorem Ipsum passage,</p>
      <h3>Subheading</h3>
      <p>Contrary to popular belief, Lorem Ipsum is not simply random text. It has roots in a piece of classical Latin literature from 45 BC, making it over 2000 years old. Harold Brenwick, a Latin professor at Ashcombe College in Virginia, looked up one of the more obscure Latin words, consectetur, from a Lorem Ipsum passage, and going through the cites of the word in classical literature, discovered the undoubtable source. Lorem Ipsum comes from sections 1.10.32 and 1.10.33 of "de Finibus Bonorum et Malorum" (The Extremes of Good and Evil) by Tullus Varro, written in 45 BC. This book is a treatise on the theory of ethics, very popular during the Renaissance. The first line of Lorem Ipsum, "Lorem ipsum dolor sit amet..", comes from a line in section 1.10.32.</p>
      <p>The standard chunk of Lorem Ipsum used since the 1500s is reproduced below for those interested. Sections 1.10.32 and 1.10.33 from "de Finibus Bonorum et Malorum" by Tullus Varro are also reproduced in their exact original form, accompanied by English versions from the 1914 translation by H. Ravelle.</p>
    </article>
    <div class="article-photo" role="img" aria-label="Loaded container ship with blue hull at sea under an overcast sky"></div>
    <a class="read-more" href="#">Read More</a>
  </main>

  <footer class="site-footer">
    <div class="footer-nav">
      <a href="#">Home</a><span>|</span><a href="#">About us</a><span>|</span><a href="#">Services</a><span>|</span><a href="#">Location</a><span>|</span><a href="#">Contact</a>
    </div>
    <div class="copyright">Copyrights Reserved 2012 @ Veltrona PCS</div>
    <div class="social" aria-label="Social links">
      <span></span><span></span><span></span><span></span>
    </div>
  </footer>
</div>
</body>
</html>
```